Upstart Retirement Planning Firm needs help with business card design

Harborview Nest Advisors, LLC is looking for help with business card design. We give advice on investments, insurance, and other financial matters related to retirement. There are some required disclosures that we will provide but mostly we are looking for a professional, classy business card that reflects the theme we have chosen. We have a logo that is attached but we would like to add a phrase; "Turning Your Earned Income Into Retirement Income"

Doubled sided only so that we can add the required disclosures (needed for our industry) on the back of the card. We will provide the exact words for this in 1-2 days.

Target Market(s)

Retirees and Pre-retirees. Professionals 50+ years old

Industry/Entity Type

Financial Planning

Contact Information for Business Card

We currently have two people who will need separate cards so we'd like to have a template so that we can add names for new cards in the future.

For the first run, please show the following information.

Gregor Pelham, MBA, ChFC®, CLU®
Financial Advisor, Registered Representative
gpelham@harborviewnest.example
Phone: (555) 318-2946
Toll Free Fax: (800) 555-0193

Address is
2187 Meadowlark Ridge Rd.
Suite K418
Virginia Beach, VA 23999

Colors
3277b5

Requirements
Must have
• Logo, contact info, small phase to describe business (in description), required legal disclosures on back of the card as follows (in small font)
• Gregor Pelham is a registered representative of and offers securities through Brightmoor Capital Brokerage Corporation, Member FNQX. Brightmoor Capital Brokerage Corporation is a member of the Brightmoor Capital Alliance which is the marketing name for Brightmoor Holding Corporation and its affiliates.
Nice to have
• Rounded edges, raised letters
Should not have
• any colors that aren't in the logo (other than black for font)

```html
<!DOCTYPE html>
<html lang="en">
<head>
<meta charset="utf-8">
<title>Harborview Nest Advisors – Business Card</title>
<link rel="stylesheet" href="https://fonts.googleapis.com/css2?family=Tinos:wght@400;700&display=swap">
<style>
  :root {
    --page-bg: #e9e7e4;
    --card-black: #161616;
    --card-white: #ffffff;
    --brand-blue: #0d5a9e;
    --brand-gray: #a7a9ac;
    --logo-gray: #5a5a5a;
    --fine-gray: #8a8a8a;
    --rule-dark: #555555;
    --text-white: #ffffff;
    --serif: "Tinos", "Times New Roman", serif;
  }
  * { box-sizing: border-box; margin: 0; padding: 0; }
  html, body {
    width: 1200px; height: 716px; overflow: hidden;
    background: var(--page-bg);
    font-family: var(--serif);
  }
  .sheet { position: relative; width: 1200px; height: 716px; }
  .card {
    position: absolute; top: 203px;
    width: 540px; height: 309px;
    border-radius: 10px; overflow: hidden;
    box-shadow: 0 6px 18px rgba(0,0,0,.18);
  }
  .card--back { left: 48px; background: var(--card-black); }
  .card--front { left: 612px; background: var(--card-white); }

  .brand-name {
    font-family: var(--serif); font-weight: 400;
    letter-spacing: 1.5px; text-align: center; white-space: nowrap;
  }

  /* Back */
  .back-brand {
    position: absolute; top: 92px; left: 0; right: 0;
    display: flex; flex-direction: column; align-items: center;
  }
  .back-brand .brand-name { color: var(--logo-gray); font-size: 30px; }
  .back-rule { margin-top: 12px; width: 320px; height: 1px; background: var(--logo-gray); }
  .disclosure {
    position: absolute; left: 44px; right: 44px; bottom: 26px;
    color: var(--fine-gray); font-size: 9.5px; line-height: 13px; text-align: center;
  }

  /* Front */
  .front-art { position: absolute; inset: 0; }
  .front-brand {
    position: absolute; top: 40px; left: 0; right: 0;
    display: flex; flex-direction: column; align-items: center;
  }
  .front-brand .brand-name { color: var(--brand-blue); font-size: 28px; }
  .front-rule { margin-top: 8px; width: 290px; height: 1px; background: var(--rule-dark); }
  .tagline {
    margin-top: 7px; color: var(--rule-dark);
    font-size: 11px; letter-spacing: .6px;
  }

  .contact {
    position: absolute; left: 24px; right: 24px; top: 174px;
    color: var(--text-white);
  }
  .contact__name { font-size: 22px; text-align: center; }
  .contact__title { font-size: 10px; text-align: center; margin: 2px 0 7px; }
  .contact__row { display: flex; gap: 16px; font-size: 14px; line-height: 21px; }
  .contact__item { display: flex; align-items: center; gap: 5px; white-space: nowrap; }
  .icon { width: 12px; height: 12px; fill: var(--text-white); }
  .contact__address { font-size: 14px; line-height: 21px; white-space: nowrap; }
</style>
</head>
<body>
<main class="sheet">

  <section class="card card--back" aria-label="Card back">
    <div class="back-brand">
      <div class="brand-name">Harborview Nest Advisors, LLC</div>
      <div class="back-rule"></div>
    </div>
    <p class="disclosure">Gregor Pelham is a registered representative of and offers securities through Brightmoor Capital Brokerage Corporation, Member FNQX. Brightmoor Capital Brokerage Corporation is a member of the Brightmoor Capital Alliance which is the marketing name for Brightmoor Holding Corporation and its affiliates.</p>
  </section>

  <section class="card card--front" aria-label="Card front">
    <svg class="front-art" width="540" height="309" viewBox="0 0 540 309">
      <path d="M0 148 C180 138 380 170 540 262 L540 309 L0 309 Z" fill="var(--brand-blue)"/>
      <path d="M0 138 C180 126 380 160 540 250" fill="none" stroke="var(--brand-gray)" stroke-width="5"/>
    </svg>

    <div class="front-brand">
      <div class="brand-name">Harborview Nest Advisors, LLC</div>
      <div class="front-rule"></div>
      <div class="tagline">Turning Your Earned Income Into Retirement Income</div>
    </div>

    <div class="contact">
      <div class="contact__name">Gregor Pelham</div>
      <div class="contact__title">MBA, ChFC®, CLU® Financial Advisor, Registered Representative</div>
      <div class="contact__row">
        <span class="contact__item">
          <svg class="icon" viewBox="0 0 12 12"><path d="M2.5 1 L4.5 1 L5.3 3.6 L4 4.6 C4.6 6 5.9 7.3 7.4 8 L8.4 6.7 L11 7.5 L11 9.5 C11 10.3 10.3 11 9.5 11 C5 11 1 7 1 2.5 C1 1.7 1.7 1 2.5 1 Z"/></svg>
          (555) 318-2946
        </span>
        <span class="contact__item">
          <svg class="icon" viewBox="0 0 12 12"><rect x="3" y="1" width="6" height="3"/><rect x="1" y="4.5" width="10" height="5" rx="1"/><rect x="3" y="8" width="6" height="3"/></svg>
          (800) 555-0193
        </span>
      </div>
      <div class="contact__row">
        <span class="contact__item">
          <svg class="icon" viewBox="0 0 12 12"><circle cx="6" cy="6" r="5" fill="none" stroke="#fff" stroke-width="1"/><ellipse cx="6" cy="6" rx="2.2" ry="5" fill="none" stroke="#fff" stroke-width="1"/><line x1="1" y1="6" x2="11" y2="6" stroke="#fff" stroke-width="1"/></svg>
          www.harborviewnest.example
        </span>
        <span class="contact__item">
          <svg class="icon" viewBox="0 0 12 12"><rect x="1" y="2.5" width="10" height="7"/><path d="M1 2.5 L6 6.5 L11 2.5" fill="none" stroke="#0d5a9e" stroke-width="1"/></svg>
          gpelham@harborviewnest.example
        </span>
      </div>
      <div class="contact__address">2187 Meadowlark Ridge Rd. Suite K418 Virginia Beach, VA 23999</div>
    </div>
  </section>

</main>
</body>
</html>
```